Golf Tournament Flyer and Header Needed

Non-profit needs a flyer for their benefit golf tournament - "Wild Socks Benefit Golf Classic"

Target Market(s)

Design and Construction industry professionals

Industry/Entity Type

Design and Construction

Colors

Designer to choose colors to be used in the design.

Requirements
Must have
• Date: September 22, 2021, 8:00 AM Shotgun Start, Location: Brookmere Links. O-VardeX Logo
Nice to have
• Would like image of golfers in crazy pants incorporated.

```html
<!DOCTYPE html>
<html lang="en">
<head>
<meta charset="utf-8">
<title>Wild Socks Benefit Golf Classic – Invitational Flyer</title>
<link rel="stylesheet" href="https://fonts.googleapis.com/css2?family=Anton&family=Montserrat:wght@500;600&family=Poppins:wght@400;700&display=swap">
<style>
  :root {
    --green-light: #78b025;
    --green-dark: #4a8410;
    --green-text: #3d7d0c;
    --gold-light: #f3d35a;
    --gold-mid: #d6ae26;
    --gold-dark: #a77f0c;
    --navy: #0d1a8a;
    --navy-deep: #06105a;
    --white: #ffffff;
    --ink: #3a3a3a;
    --icon-blue: #1d4f8c;
    --sky: #8fc2ea;
    --turf: #5d8a3a;
  }
  html, body {
    margin: 0;
    padding: 0;
    width: 863px;
    height: 1200px;
    overflow: hidden;
    background: var(--green-dark);
  }
  .flyer {
    display: block;
    width: 863px;
    height: 1200px;
  }
  .invitational {
    font-family: "Montserrat", sans-serif;
    font-weight: 500;
    font-size: 40px;
    fill: var(--white);
  }
  .event-title {
    font-family: "Anton", sans-serif;
    font-size: 104px;
    fill: var(--white);
  }
  .event-title-shadow {
    font-family: "Anton", sans-serif;
    font-size: 104px;
    fill: #555b66;
  }
  .brand-name {
    font-family: "Poppins", sans-serif;
    font-weight: 400;
    font-size: 24px;
    fill: var(--ink);
  }
  .details {
    font-family: "Poppins", sans-serif;
    font-weight: 400;
    font-size: 25px;
    fill: var(--ink);
  }
  .details .accent {
    font-weight: 700;
    fill: var(--green-text);
  }
</style>
</head>
<body>
<svg class="flyer" viewBox="0 0 863 1200" xmlns="http://www.w3.org/2000/svg">
  <defs>
    <linearGradient id="field" x1="0" y1="0" x2="1" y2="1">
      <stop offset="0" stop-color="var(--green-light)"/>
      <stop offset="1" stop-color="var(--green-dark)"/>
    </linearGradient>
    <linearGradient id="gold" x1="0" y1="0" x2="1" y2="0">
      <stop offset="0" stop-color="var(--gold-mid)"/>
      <stop offset="0.5" stop-color="var(--gold-light)"/>
      <stop offset="1" stop-color="var(--gold-mid)"/>
    </linearGradient>
    <linearGradient id="navy" x1="0" y1="0" x2="1" y2="0">
      <stop offset="0" stop-color="var(--navy-deep)"/>
      <stop offset="0.5" stop-color="var(--navy)"/>
      <stop offset="1" stop-color="var(--navy-deep)"/>
    </linearGradient>
    <linearGradient id="photo-tones" x1="0" y1="0" x2="0" y2="1">
      <stop offset="0" stop-color="var(--sky)"/>
      <stop offset="0.45" stop-color="#c9d6e4"/>
      <stop offset="0.75" stop-color="#6f93c8"/>
      <stop offset="1" stop-color="var(--turf)"/>
    </linearGradient>
    <clipPath id="photo-clip">
      <rect x="0" y="0" width="863" height="1000"/>
    </clipPath>
    <path id="arc-invitational" d="M160,258 Q432,154 704,258"/>
    <path id="arc-title" d="M130,410 Q432,322 734,410"/>
  </defs>

  <!-- background field -->
  <rect class="field" width="863" height="1200" fill="url(#field)"/>

  <!-- gold frame -->
  <rect class="frame" x="26" y="71" width="813" height="1104" fill="none" stroke="var(--gold-mid)" stroke-width="5"/>

  <!-- photo of golfers in patterned trousers -->
  <g class="photo" clip-path="url(#photo-clip)" role="img" aria-label="Photo of four golfers in white polos and blue diamond-patterned trousers on a golf course">
    <circle cx="438" cy="809" r="313" fill="url(#photo-tones)" stroke="var(--white)" stroke-width="5"/>
  </g>

  <!-- white info panel -->
  <path class="info-panel" d="M0,1067 Q100,1010 182,976 Q440,905 703,972 Q770,1010 863,1067 Q720,1010 650,1025 Q580,1119 431,1119 Q282,1119 213,1025 Q143,1010 0,1067 Z" fill="var(--white)"/>
  <path class="info-panel-edge" d="M182,976 Q440,905 703,972" fill="none" stroke="var(--green-text)" stroke-width="6"/>

  <!-- navy banner -->
  <path class="banner" d="M160,212 Q432,55 704,212 L721,312 Q432,170 143,312 Z" fill="url(#navy)"/>
  <text class="invitational" letter-spacing="10">
    <textPath href="#arc-invitational" startOffset="50%" text-anchor="middle">INVITATIONAL</textPath>
  </text>

  <!-- gold ribbon tails -->
  <polygon class="ribbon-tail" points="88,347 200,347 200,533 53,533 100,440" fill="url(#gold)"/>
  <polygon class="ribbon-fold" points="143,470 200,533 200,470" fill="var(--gold-dark)"/>
  <polygon class="ribbon-tail" points="776,347 664,347 664,533 811,533 764,440" fill="url(#gold)"/>
  <polygon class="ribbon-fold" points="721,470 664,533 664,470" fill="var(--gold-dark)"/>

  <!-- gold ribbon band -->
  <path class="ribbon" d="M143,312 Q432,170 721,312 L721,470 Q432,330 143,470 Z" fill="url(#gold)"/>

  <!-- event title -->
  <text class="event-title-shadow" transform="translate(4,6)">
    <textPath href="#arc-title" startOffset="50%" text-anchor="middle">WILD SOCKS</textPath>
  </text>
  <text class="event-title">
    <textPath href="#arc-title" startOffset="50%" text-anchor="middle">WILD SOCKS</textPath>
  </text>

  <!-- brand box -->
  <rect class="brand-box" x="359" y="15" width="145" height="128" fill="var(--white)" stroke="var(--gold-mid)" stroke-width="5"/>
  <circle class="brand-dot" cx="431" cy="64" r="26" fill="var(--icon-blue)"/>
  <text class="brand-name" x="431" y="124" text-anchor="middle">O-VardeX</text>

  <!-- event details -->
  <g class="detail-icons" fill="var(--icon-blue)">
    <path class="icon-pin" d="M306,981 a9,9 0 0 1 18,0 c0,8 -9,17 -9,17 c0,0 -9,-9 -9,-17 Z M315,977 a4,4 0 1 0 0.01,0 Z" fill-rule="evenodd"/>
    <circle class="icon-clock" cx="285" cy="1018" r="11"/>
    <path d="M285,1011 v7 h5" stroke="var(--white)" stroke-width="2" fill="none"/>
    <rect class="icon-calendar" x="298" y="1051" width="20" height="16" rx="2"/>
    <rect x="298" y="1046" width="20" height="4" rx="1"/>
  </g>
  <text class="details" x="332" y="996">Brookmere <tspan class="accent">Links</tspan></text>
  <text class="details" x="304" y="1027">8:00 AM <tspan class="accent">Shotgun Start</tspan></text>
  <text class="details" x="326" y="1066">September <tspan class="accent">22, 2021</tspan></text>
</svg>
</body>
</html>
```